Stationary Design for Quince consultant and support company

We need new stationary designed for a London based support company that provide on-site and remote support services for Quince products. Our clients are both consumers and businesses.

We would like a letterhead, compliment slip, business card and possibly an e-mail signature designed.

Business card designs can be either 1 side or 2, depending on designs we receive we may choose a preference for 1 or 2 sides later on in the design stage.

Designs needs to be at least 300dpi and should be done using CMYK colours.

We want the design to be bold, easy to read, clean and professional.

We have attached our company logo in 2 colour variations (if you need any other source files then please ask).

Our logo colours are as follows:

Blue (85, 50, 0, 0) and Green (50, 0, 100, 0)

We use two different suppliers for out stationary so here are the size dimensions for both. Unfortunately they are ever so slightly different size wise so hopefully we can get something that accommodates both, we can provide dimensions if required for final versions.

Some fonts that have been used before with our company are Probert (for tagline on our company logo) and previously had Nauman used, however we are very much open to seeing what the designers come up with and the fonts mentioned are not a requirement.
Updates

Company details for designs (however the template should be editable for multiple staff) Lumora Ltd. Registered Office: 62-70 Harrowfield Lane London N7 3QD 020 7591 3384 www.lumora-it.example info@lumora-it.example Company is Registered in England and Wales Company No. 07342519 Directors details (if you want to make the template using his details), rest of the details are as above Dan Frost Director dan@lumora-it.example

Hi all, Thank you for your submissions so far. Could we please ask that you don't use the logo with the tagline from our website for the stationary designs and only the logos provided in the design brief. For the business cards we are looking at normal rectangular business cards to be used and we can provide a template guide for size if needed, please just ask. Regards Lumora Team

Target Market(s)

Our target market are consumers (of all ages) and small/medium businesses.

Industry/Entity Type

Business

Font styles to use
Serif
Sans Serif

Requirements
Must have
• At least business card, letterhead and compliment slip submitted (we need all 3 designed this time round)
Should not have
• Business cards should not have the writing "registered office" (letterheads and compliment slips can along the bottom edge)

```html
<!DOCTYPE html>
<html lang="en">
<head>
<meta charset="utf-8">
<title>Lumora – Compliment Slip</title>
<link href="https://fonts.googleapis.com/css2?family=Didact+Gothic&family=Montserrat:wght@700&display=swap" rel="stylesheet">
<style>
  :root {
    --backdrop: #5b5b5b;
    --paper: #ffffff;
    --ink: #1e1e1e;
    --brand-blue: #1f5fb4;
    --brand-green: #7ab928;
    --accent-tint-blue: #e9f0fa;
    --accent-tint-green: #eef6e2;
    --muted: #333333;
  }
  html, body {
    margin: 0;
    padding: 0;
    width: 1200px;
    height: 1000px;
    overflow: hidden;
    background: var(--backdrop);
  }
  .canvas {
    position: relative;
    width: 1200px;
    height: 1000px;
  }
  .compliment-slip {
    position: absolute;
    left: 207px;
    top: 322px;
    width: 793px;
    height: 356px;
    background: var(--paper);
    overflow: hidden;
    box-shadow: 3px 4px 6px rgba(0,0,0,0.35);
  }
  .accent-field {
    position: absolute;
    left: 401px;
    top: 0;
    width: 392px;
    height: 356px;
    background: linear-gradient(100deg, rgba(255,255,255,0) 0%, var(--accent-tint-blue) 55%, var(--accent-tint-green) 100%);
  }
  .brand-name {
    position: absolute;
    left: 52px;
    top: 54px;
    margin: 0;
    font-family: "Montserrat", sans-serif;
    font-weight: 700;
    font-size: 34px;
    letter-spacing: 3px;
    line-height: 1;
    color: var(--ink);
    text-transform: uppercase;
  }
  .slip-title {
    position: absolute;
    left: 54px;
    top: 279px;
    margin: 0;
    font-family: "Didact Gothic", sans-serif;
    font-weight: 400;
    font-size: 19.5px;
    line-height: 1.2;
    letter-spacing: 0.3px;
    color: var(--ink);
  }
  .contact-list {
    position: absolute;
    left: 51px;
    top: 317px;
    margin: 0;
    padding: 0;
    list-style: none;
    display: flex;
    gap: 16px;
    font-family: "Didact Gothic", sans-serif;
    font-size: 11px;
    line-height: 1.2;
    color: var(--muted);
  }
  .contact-item {
    display: flex;
    align-items: center;
    gap: 6px;
  }
  .contact-icon {
    width: 12px;
    height: 12px;
  }
</style>
</head>
<body>
<main class="canvas">
  <section class="compliment-slip" aria-label="Lumora compliment slip">
    <div class="accent-field" role="img" aria-label="Soft blue and green brand accent area"></div>

    <h1 class="brand-name">Lumora</h1>

    <h2 class="slip-title">WITH COMPLIMENTS</h2>

    <ul class="contact-list">
      <li class="contact-item">
        <svg class="contact-icon" viewBox="0 0 12 12" aria-hidden="true">
          <g fill="none" stroke="var(--brand-blue)" stroke-width="1">
            <circle cx="6" cy="6" r="5"/>
            <ellipse cx="6" cy="6" rx="2.2" ry="5"/>
            <line x1="1" y1="6" x2="11" y2="6"/>
          </g>
        </svg>
        <span>www.lumora-it.example</span>
      </li>
      <li class="contact-item">
        <svg class="contact-icon" viewBox="0 0 12 12" aria-hidden="true">
          <circle cx="6" cy="6" r="5.4" fill="none" stroke="var(--brand-blue)" stroke-width="1"/>
          <rect x="3.3" y="4.2" width="5.4" height="3.8" fill="var(--brand-blue)"/>
          <polyline points="3.3,4.2 6,6.3 8.7,4.2" fill="none" stroke="#fff" stroke-width="0.6"/>
        </svg>
        <span>info@lumora-it.example</span>
      </li>
    </ul>
  </section>
</main>
</body>
</html>
```